New Webpage for High Class Expert Witness Services Company

We are looking for a minimalist design for a webpage that just has our logo and an entry form offer to connect with one of our Liaisons.
The entry form should just ask for Name, Email, Contact Info and Description of Project.

Company Name is: The Marlowe Crest Advisory Services

Number of Pages Required

1 page

```html
<!DOCTYPE html>
<html lang="en">
<head>
<meta charset="utf-8">
<title>Marlowe Crest Advisory Services</title>
<link rel="stylesheet" href="https://fonts.googleapis.com/css2?family=PT+Serif:wght@400;700&family=Roboto:wght@400;500&display=swap">
<style>
  :root{
    --bg:#141414;
    --bg-soft:#1e1e1e;
    --silver:#d9d9d9;
    --silver-dark:#8f8f8f;
    --white:#f4f4f4;
    --rule:#8a8a8a;
    --field:#1c1c1c;
    --field-border:#4a4a4a;
    --placeholder:#8c8c8c;
  }
  *{margin:0;padding:0;box-sizing:border-box}
  html,body{width:1200px;height:1131px;overflow:hidden;background:var(--bg)}
  .page{
    position:relative;width:1200px;height:1131px;overflow:hidden;
    background:radial-gradient(ellipse at 30% 40%,#1f1f1f 0%,var(--bg) 55%),var(--bg);
    font-family:"Roboto",sans-serif;color:var(--white);
  }
  .brand{
    position:absolute;left:0;right:0;top:52px;text-align:center;
    font-family:"PT Serif",serif;font-weight:400;color:var(--silver);
  }
  .brand-name{font-size:42px;letter-spacing:2px;line-height:48px;text-transform:uppercase}
  .brand-sub{font-size:24px;letter-spacing:6px;line-height:30px;text-transform:uppercase}
  .headline{
    position:absolute;left:0;right:0;top:206px;text-align:center;
    font-family:"PT Serif",serif;font-weight:700;font-size:53px;line-height:62px;
    background:linear-gradient(90deg,#a9a9a9,#f0f0f0 45%,#b8b8b8);
    -webkit-background-clip:text;background-clip:text;color:transparent;
  }
  .intro{
    position:absolute;left:0;right:0;top:352px;text-align:center;
    font-size:19px;font-weight:500;line-height:32px;
  }
  .rule{position:absolute;left:118px;width:970px;height:2px;background:var(--rule)}
  .rule.top{top:446px}
  .rule.bottom{top:1082px;left:114px;width:972px}
  .about-title{
    position:absolute;left:111px;top:530px;font-size:51px;font-weight:500;
    background:linear-gradient(90deg,#8d8d8d,#f2f2f2);
    -webkit-background-clip:text;background-clip:text;color:transparent;
  }
  .about-lead{position:absolute;left:111px;top:608px;font-size:22px;font-weight:500}
  .about-text{
    position:absolute;left:111px;top:647px;width:440px;
    font-size:15.5px;line-height:31.7px;text-align:justify;
  }
  .feature{position:absolute;display:flex;align-items:center;gap:16px;font-size:20px;font-weight:500;line-height:26px}
  .feature svg{flex:none;width:54px;height:62px}
  .f1{left:111px;top:845px}
  .f2{left:343px;top:845px}
  .f3{left:111px;top:952px}
  .f4{left:343px;top:952px}
  .consult{
    position:absolute;left:645px;top:509px;width:443px;height:529px;border-radius:6px;
    background:linear-gradient(160deg,#5a5a5a 0%,#2c2c2c 40%,#1d1d1d 70%,#353535 100%);
  }
  .field{
    position:absolute;left:27px;width:398px;height:54px;
    background:var(--field);border:2px solid var(--field-border);border-radius:5px;
    display:flex;align-items:center;gap:12px;padding-left:12px;
    color:var(--placeholder);font-size:15px;
  }
  .field svg{width:18px;height:18px;fill:var(--placeholder)}
  .field.name{top:47px}
  .field.email{top:107px}
  .field.phone{top:176px}
  .field.desc{top:244px;height:174px;align-items:flex-start;padding-top:18px}
  .submit{
    position:absolute;left:30px;top:436px;width:393px;height:56px;border-radius:3px;
    background:linear-gradient(170deg,#8a8a8a 0%,#bdbdbd 35%,#f2f2f2 60%,#dcdcdc 100%);
    display:flex;align-items:center;justify-content:center;
    color:#111;font-size:15px;font-weight:500;letter-spacing:.2px;
  }
  .copyright{position:absolute;left:0;right:0;top:1100px;text-align:center;font-size:12.5px}
</style>
</head>
<body>
<div class="page">
  <div class="brand">
    <div class="brand-name">Marlowe Crest</div>
    <div class="brand-sub">Advisory Services</div>
  </div>

  <h1 class="headline">Precision Placement of<br>Distinguished Expert Witnesses</h1>
  <p class="intro">Confidential access to highly qualified expert witnesses and<br>defense specialists across multiple disciplines</p>
  <div class="rule top"></div>

  <h2 class="about-title">About Us</h2>
  <h3 class="about-lead">Trusted Experts. Strategic Results.</h3>
  <p class="about-text">The Marlowe Crest Advisory Services connects attorneys, insurers, and organizations with highly qualified expert witnesses and defense specialists across multiple disciplines. We provide discreet, professional liaison services designed to strengthen complex cases with credible expertise.</p>

  <div class="feature f1">
    <svg viewBox="0 0 54 62"><defs><linearGradient id="sh" x1="0" y1="0" x2="1" y2="1"><stop offset="0" stop-color="#f0f0f0"/><stop offset="1" stop-color="#8a8a8a"/></linearGradient></defs><path d="M27 2 L50 10 V32 C50 46 40 55 27 60 C14 55 4 46 4 32 V10 Z" fill="url(#sh)"/><rect x="17" y="24" width="16" height="18" rx="2" fill="#1a1a1a"/><rect x="27" y="33" width="10" height="9" rx="1" fill="#1a1a1a" stroke="#ddd" stroke-width="1"/><path d="M29 33 v-3 a3 3 0 0 1 6 0 v3" fill="none" stroke="#1a1a1a" stroke-width="2"/></svg>
    <span>Confidential</span>
  </div>
  <div class="feature f2">
    <svg viewBox="0 0 54 62"><path d="M27 2 L50 10 V32 C50 46 40 55 27 60 C14 55 4 46 4 32 V10 Z" fill="url(#sh)"/><circle cx="29" cy="34" r="11" fill="none" stroke="#1a1a1a" stroke-width="3"/><rect x="26" y="18" width="6" height="4" fill="#1a1a1a"/><path d="M30 27 l-4 8 h4 l-2 6" fill="none" stroke="#1a1a1a" stroke-width="2"/><path d="M10 30h6M9 35h6M11 40h5" stroke="#1a1a1a" stroke-width="1.5"/></svg>
    <span>Rapid Response</span>
  </div>
  <div class="feature f3">
    <svg viewBox="0 0 54 62"><path d="M27 2 L50 10 V32 C50 46 40 55 27 60 C14 55 4 46 4 32 V10 Z" fill="url(#sh)"/><circle cx="27" cy="36" r="11" fill="#1a1a1a"/><path d="M27 16 a6 6 0 0 1 6 6 c0 4 -6 10 -6 10 s-6 -6 -6 -10 a6 6 0 0 1 6 -6z" fill="#1a1a1a" stroke="#ddd" stroke-width="1"/><circle cx="27" cy="22" r="2" fill="#ddd"/></svg>
    <span>Nationwide<br>Network</span>
  </div>
  <div class="feature f4">
    <svg viewBox="0 0 54 62"><path d="M27 2 L50 10 V32 C50 46 40 55 27 60 C14 55 4 46 4 32 V10 Z" fill="url(#sh)"/><rect x="14" y="24" width="26" height="20" rx="2" fill="#1a1a1a"/><path d="M21 24 v-4 h12 v4" fill="none" stroke="#1a1a1a" stroke-width="2.5"/><rect x="17" y="31" width="20" height="2" fill="#ddd"/><rect x="17" y="37" width="20" height="2" fill="#ddd"/></svg>
    <span>Courtroom Proven<br>Experts</span>
  </div>

  <form class="consult">
    <div class="field name"><svg viewBox="0 0 24 24"><circle cx="12" cy="7" r="5"/><path d="M2 23c0-6 4-9 10-9s10 3 10 9z"/></svg>First Name</div>
    <div class="field email"><svg viewBox="0 0 24 24"><path d="M1 4h22v16H1z"/><path d="M1 4l11 9 11-9" fill="none" stroke="#1c1c1c" stroke-width="2"/></svg>Email Address</div>
    <div class="field phone"><svg viewBox="0 0 24 24"><path d="M6 1l4 5-2 3c1 3 4 6 7 7l3-2 5 4-3 4C10 22 2 14 2 4z"/></svg>Contact Number</div>
    <div class="field desc"><svg viewBox="0 0 24 24"><path d="M3 1h14v9l-6 8v4H3z"/><path d="M6 6h8M6 10h8M6 14h4" stroke="#1c1c1c" stroke-width="2"/><path d="M20 10l3 3-8 9h-3v-3z"/></svg>Description of Project</div>
    <div class="submit">REQUEST A CONSULTATION</div>
  </form>

  <div class="rule bottom"></div>
  <p class="copyright">Copyright © 2026 Marlowe Crest Advisory Services . All rights reserved.</p>
</div>
</body>
</html>
```